NEW Wordpress Website Design for a Dynamic Long Term Healthcare Company in Hawaii

I would like a new website design for my current company, Marlow Health Collective, which has two different brands - Marlow Homecare and Marlow Senior Living. You can see the current website at www.marlowhealth-example.com. The website should be built using Wordpress Software and the Framewise theme. The website should have a local Hawaii island/tropical feel, but look professional for healthcare. I'm looking for something fresh, and want the designer to select colors, styles, etc.

In the Header, on all pages, I would like a menu that includes Home Care, Senior Living, Rates, and About Us.
Under each of the Header Menu Titles, I would like these drop downs included:
Home Care (drop down pages)- Nurse Aide Care, 24-Hour Home Care, Skilled Nursing, Lifestyle Aide, Hospice at Home, Bathing & Meal Service.
Senior Living (drop down pages) - Long-Term Stay, Short-Term Stay.
Rates (drop down page) - Rates.
About Us (drop down pages) - Our Mission, Ohana Talk, About Dana Marlow.

In the footer, on all pages, you should include the address: 248 Pueo Lane, Suite 310, Honolulu, HI 96817. Phone number: 808-555-0172
The footer should also include buttons for a page called Learn, Caregiver Jobs, and each of the service page links to include: Nurse Aide Care, 24-Hour Home Care, Skilled Nursing, Lifestyle Aide, Hospice at Home, Bathing & Meal Service.
Please don't take the current website and redesign a few aspects. I'm looking for a completely different look and feel.

Target Market(s)

40-80 year olds

Industry/Entity Type

Long Term Healthcare

Coding

Coded - Design and coding required

Requirements
Should not have
• Our existing website as a template. We are looking for a complete redesign. Thank you.

```html
<!DOCTYPE html>
<html lang="en">
<head>
<meta charset="utf-8">
<title>Marlow Health Collective</title>
<link href="https://fonts.googleapis.com/css2?family=DM+Sans:wght@400;500;600;700&display=swap" rel="stylesheet">
<style>
:root{
  --coral:#f47f74;
  --coral-card:#f5867b;
  --coral-soft:#fbd3cf;
  --ink:#1f1f1f;
  --muted:#6f6f6f;
  --line:#e6e6e6;
  --blush:#fdf8f8;
  --grey-bg:#f5f5f5;
  --card:#f7f7f7;
  --white:#ffffff;
}
*{box-sizing:border-box;margin:0;padding:0}
html,body{width:1200px;height:3997px;overflow:hidden}
body{font-family:"DM Sans",sans-serif;color:var(--ink);background:var(--white);position:relative}
.abs{position:absolute}
.btn-outline{position:absolute;border:1.5px solid var(--coral);color:var(--coral);border-radius:30px;display:flex;align-items:center;justify-content:center;font-size:15px;font-weight:500;background:transparent}
.btn-solid{position:absolute;background:var(--coral);color:var(--white);border-radius:30px;display:flex;align-items:center;justify-content:center;font-size:15px;font-weight:500}

/* header */
.site-header{position:absolute;left:0;top:0;width:1200px;height:100px;background:var(--white)}
.brand{position:absolute;top:32px;font-size:19px;font-weight:700;color:var(--coral);display:flex;align-items:center;gap:8px}
.brand .dot{width:12px;height:12px;border-radius:50%;background:var(--coral)}
.main-nav{position:absolute;left:382px;top:40px;display:flex;gap:30px;font-size:15px;color:#555}
.main-nav span.active{color:var(--coral)}
.main-nav .caret::after{content:"";display:inline-block;width:5px;height:5px;border-right:1.3px solid #666;border-bottom:1.3px solid #666;transform:rotate(45deg);margin-left:6px;position:relative;top:-3px}

/* hero */
.hero{position:absolute;left:0;top:100px;width:1200px;height:525px;background:linear-gradient(120deg,#8a6a3b 0%,#b59a54 35%,#c94b4b 60%,#4f7fb6 80%,#c7b27c 100%)}
.hero::after{content:"";position:absolute;inset:0;background:linear-gradient(90deg,rgba(40,25,10,.55),rgba(40,25,10,.1))}
.hero-copy{position:absolute;left:84px;z-index:2;color:var(--white)}
.hero h1{top:80px;font-size:45px;line-height:58px;font-weight:700;letter-spacing:1px;text-transform:uppercase;width:480px}
.hero p{top:268px;font-size:16px;line-height:25px;width:520px}
.scroll-ind{position:absolute;left:583px;top:448px;width:40px;height:60px;border:2px solid rgba(255,255,255,.9);border-radius:20px;z-index:2}
.scroll-ind::after{content:"";position:absolute;left:18px;top:12px;width:2px;height:16px;background:var(--white)}

/* sections */
.blush-band{position:absolute;left:0;top:625px;width:1200px;height:1210px;background:var(--blush)}
.eyebrow{position:absolute;font-size:16px;color:var(--coral)}
.sec-title{position:absolute;font-size:31px;font-weight:600;line-height:41px;color:var(--ink)}
.service-card{position:absolute;width:450px;background:var(--card);border-radius:18px;padding:0 27px;display:flex;flex-direction:column;justify-content:center}
.service-card h3{font-size:18px;font-weight:600;margin-bottom:8px}
.service-card p{font-size:14px;color:var(--muted)}
.service-card.featured{background:var(--white);border:1px solid var(--line);flex-direction:row;align-items:center;justify-content:flex-start;gap:30px;padding-left:34px}
.badge{width:64px;height:64px;border-radius:50%;background:var(--coral);color:var(--white);display:flex;align-items:center;justify-content:center;font-size:30px;font-weight:500;flex:none}
.service-card.featured h3{color:var(--coral);font-weight:500}
.photo{position:absolute}

/* rates */
.rates-band{position:absolute;left:0;top:1836px;width:1200px;height:970px;background:var(--grey-bg)}
.rates-title{position:absolute;left:0;width:1200px;top:1912px;text-align:center;font-size:34px;font-weight:700;letter-spacing:-.5px}
.rates-desc{position:absolute;left:250px;width:700px;top:1966px;text-align:center;font-size:14.5px;line-height:23px;color:#555}
.tabs{position:absolute;left:428px;top:2045px;width:343px;height:52px;background:#ececec;border-radius:6px}
.tabs span{position:absolute;top:9px;height:34px;display:flex;align-items:center;font-size:15px}
.price-card{position:absolute;top:2147px;width:310px;height:621px;background:var(--coral-card);border-radius:24px;color:var(--white);text-align:center}
.price-card h4{position:absolute;top:52px;left:40px;width:230px;font-size:16px;font-weight:400;line-height:22px}
.price-card .amount{position:absolute;top:110px;width:100%;font-size:44px;font-weight:700}
.price-card .blurb{position:absolute;top:180px;left:40px;width:230px;font-size:14px;line-height:22px}
.price-card ul{position:absolute;top:272px;left:60px;list-style:none;text-align:left}
.price-card li{font-size:14px;height:37.5px;display:flex;align-items:center;gap:12px}
.price-card li svg{flex:none}
.price-card .call{position:absolute;left:49px;top:533px;width:212px;height:48px;background:var(--white);color:var(--ink);border-radius:6px;display:flex;align-items:center;justify-content:center;font-size:15px}

/* about */
.about-body{position:absolute;left:84px;top:2990px;width:530px;font-size:13.5px;line-height:25px;color:#555}

/* cta */
.cta{position:absolute;left:40px;top:3302px;width:1119px;height:273px;border-radius:10px;background:linear-gradient(90deg,#6b3a2a,#a4553f 45%,#7c6a4a 75%,#4d6b3f);overflow:hidden}
.cta::after{content:"";position:absolute;inset:0;background:rgba(40,20,15,.35)}
.cta-inner{position:absolute;inset:0;z-index:2;color:var(--white);text-align:center}
.cta h2{position:absolute;top:50px;width:100%;font-size:36px;font-weight:600}
.cta p{position:absolute;top:126px;left:100px;width:919px;font-size:15.5px;line-height:21px}

/* footer */
.foot-brand{position:absolute;top:3665px;font-size:22px;font-weight:700;display:flex;align-items:center;gap:8px}
.foot-brand .sq{width:14px;height:14px;background:currentColor}
.foot-rule{position:absolute;left:84px;top:3738px;width:1033px;height:1px;background:var(--line)}
.foot-head{position:absolute;top:3773px;font-size:16px;font-weight:600;color:var(--coral)}
.foot-col{position:absolute;top:3807px;font-size:12.5px;color:var(--coral);line-height:32px;opacity:.85}
.contact-row{position:absolute;left:480px;font-size:12.5px;color:var(--coral);display:flex;gap:12px;line-height:16px;opacity:.85}
.copyright{position:absolute;top:3960px;left:0;width:1200px;text-align:center;font-size:12px;color:var(--coral)}
</style>
</head>
<body>

<header class="site-header">
  <div class="brand" style="left:84px"><span class="dot"></span>Marlow Homecare</div>
  <nav class="main-nav">
    <span class="active">Home</span>
    <span class="caret">Home care</span>
    <span class="caret">Senior Living</span>
    <span class="caret">Rates</span>
    <span class="caret">About Us</span>
  </nav>
  <div class="btn-outline" style="left:1009px;top:30px;width:108px;height:36px;font-size:13px">Contact us</div>
</header>

<section class="hero" role="img" aria-label="Photo of a caregiver leading seniors in a light dumbbell exercise in a sunlit living room">
  <h1 class="hero-copy">Hawaii's Choice Homecare &amp; Senior Living</h1>
  <p class="hero-copy">Marlow Homecare provides a variety of professional in-home health care services throughout the entire island of Oahu. Marlow Senior Living, a beautiful Adult Residential Care Home, is located on the windward side of Oahu in Kailua.</p>
  <div class="btn-solid" style="left:84px;top:388px;width:181px;height:52px;z-index:2">Contact us</div>
  <div class="scroll-ind"></div>
</section>

<div class="blush-band"></div>

<!-- Home care overview -->
<div class="eyebrow" style="left:84px;top:678px">Home Care</div>
<h2 class="sec-title" style="left:84px;top:706px">Homecare Services Overview</h2>
<div class="abs" style="left:69px;top:784px;width:4px;height:438px;background:#dcdcdc;border-radius:2px"></div>
<div class="abs" style="left:69px;top:784px;width:4px;height:285px;background:var(--coral);border-radius:2px"></div>
<div class="service-card featured" style="left:84px;top:784px;height:133px">
  <div class="badge">24</div>
  <div><h3>24-Hour Home Care</h3><p>It has roots in a piece of classical</p></div>
</div>
<div class="service-card" style="left:84px;top:920px;height:102px"><h3>Nurse Aide Care</h3><p>Lorem Ipsum is not simply random text</p></div>
<div class="service-card" style="left:84px;top:1026px;height:102px"><h3>Skilled Nursing</h3><p>Lorem Ipsum is not simply random text</p></div>
<div class="service-card" style="left:84px;top:1132px;height:102px"><h3>Lifestyle Aide</h3><p>Lorem Ipsum is not simply random text</p></div>
<div class="photo" role="img" aria-label="Photo of a nurse helping a senior man dress at his bedside" style="left:600px;top:784px;width:600px;height:491px;border-radius:10px 0 0 10px;background:linear-gradient(135deg,#d9cc5a,#c7b856 45%,#9a8b4e 75%,#d8c9a4)"></div>
<div class="btn-outline" style="left:83px;top:1275px;width:182px;height:51px">Call today</div>

<!-- Senior living overview -->
<div class="photo" role="img" aria-label="Photo of a caregiver walking with a woman using a walker on a tropical garden path" style="left:0;top:1363px;width:597px;height:473px;border-radius:0 10px 10px 0;background:linear-gradient(135deg,#4f7a2f,#86a75a 40%,#c9c6b2 70%,#6f8a4a)"></div>
<div class="eyebrow" style="left:630px;top:1364px">Senior Living</div>
<h2 class="sec-title" style="left:630px;top:1390px;width:420px">Senior Living Services Overview</h2>
<div class="service-card featured" style="left:630px;top:1510px;height:131px">
  <div class="badge">24</div>
  <div><h3>Long-Term Stay</h3><p>It has roots in a piece of classical</p></div>
</div>
<div class="service-card" style="left:630px;top:1645px;height:103px"><h3>Short-Term Stay</h3><p>Lorem Ipsum is not simply random text</p></div>
<div class="btn-outline" style="left:630px;top:1764px;width:182px;height:51px">Call today</div>

<!-- Rates -->
<div class="rates-band"></div>
<h2 class="rates-title">Our Rates</h2>
<p class="rates-desc">Korem ipsum dolor sit amet, consectetur adipiscing elit. Nunc vulputate libero et velit interdum, ac aliquet odio mattis.</p>
<div class="tabs">
  <span style="left:18px;color:#777">Homecare Services</span>
  <span style="left:210px;width:125px;justify-content:center;background:var(--coral-soft);color:var(--coral);border-radius:4px;font-weight:500">Senior Living</span>
</div>

<div class="price-card" style="left:273px">
  <h4>Senior Living - Long Term Stay</h4>
  <div class="amount">$14.50</div>
  <p class="blurb">Rorem ipsum dolor sit amet, consectetur adipiscing elit.</p>
  <ul>
    <li><svg width="20" height="20" viewBox="0 0 20 20"><circle cx="10" cy="10" r="10" fill="#fff"/><path d="M5.5 10.2l3 3 6-6" fill="none" stroke="#f5867b" stroke-width="2"/></svg>Sorem ipsum dolor sit</li>
    <li><svg width="20" height="20" viewBox="0 0 20 20"><circle cx="10" cy="10" r="10" fill="#fff"/><path d="M5.5 10.2l3 3 6-6" fill="none" stroke="#f5867b" stroke-width="2"/></svg>Forem ipsum dolor sit</li>
    <li><svg width="20" height="20" viewBox="0 0 20 20"><circle cx="10" cy="10" r="10" fill="#fff"/><path d="M5.5 10.2l3 3 6-6" fill="none" stroke="#f5867b" stroke-width="2"/></svg>Yorem ipsum dolor sit</li>
    <li><svg width="20" height="20" viewBox="0 0 20 20"><circle cx="10" cy="10" r="10" fill="#fff"/><path d="M5.5 10.2l3 3 6-6" fill="none" stroke="#f5867b" stroke-width="2"/></svg>Jorem ipsum dolor sit</li>
    <li><svg width="20" height="20" viewBox="0 0 20 20"><circle cx="10" cy="10" r="10" fill="#fff"/><path d="M5.5 10.2l3 3 6-6" fill="none" stroke="#f5867b" stroke-width="2"/></svg>Morem ipsum dolor sit</li>
    <li><svg width="20" height="20" viewBox="0 0 20 20"><circle cx="10" cy="10" r="10" fill="#fff"/><path d="M5.5 10.2l3 3 6-6" fill="none" stroke="#f5867b" stroke-width="2"/></svg>Worem ipsum dolor sit</li>
  </ul>
  <div class="call">Call now</div>
</div>

<div class="price-card" style="left:617px">
  <h4>Senior Living - Short Term Stay</h4>
  <div class="amount">$14.50</div>
  <p class="blurb">Vorem ipsum dolor sit amet, consectetur adipiscing elit.</p>
  <ul>
    <li><svg width="20" height="20" viewBox="0 0 20 20"><circle cx="10" cy="10" r="10" fill="#fff"/><path d="M5.5 10.2l3 3 6-6" fill="none" stroke="#f5867b" stroke-width="2"/></svg>Jorem ipsum dolor sit</li>
    <li><svg width="20" height="20" viewBox="0 0 20 20"><circle cx="10" cy="10" r="10" fill="#fff"/><path d="M5.5 10.2l3 3 6-6" fill="none" stroke="#f5867b" stroke-width="2"/></svg>Dorem ipsum dolor sit</li>
    <li><svg width="20" height="20" viewBox="0 0 20 20"><circle cx="10" cy="10" r="10" fill="#fff"/><path d="M5.5 10.2l3 3 6-6" fill="none" stroke="#f5867b" stroke-width="2"/></svg>Yorem ipsum dolor sit</li>
    <li><svg width="20" height="20" viewBox="0 0 20 20"><circle cx="10" cy="10" r="10" fill="#fff"/><path d="M5.5 10.2l3 3 6-6" fill="none" stroke="#f5867b" stroke-width="2"/></svg>Worem ipsum dolor sit</li>
    <li><svg width="20" height="20" viewBox="0 0 20 20"><circle cx="10" cy="10" r="10" fill="#fff"/><path d="M5.5 10.2l3 3 6-6" fill="none" stroke="#f5867b" stroke-width="2"/></svg>Corem ipsum dolor sit</li>
    <li><svg width="20" height="20" viewBox="0 0 20 20"><circle cx="10" cy="10" r="10" fill="#fff"/><path d="M5.5 10.2l3 3 6-6" fill="none" stroke="#f5867b" stroke-width="2"/></svg>Korem ipsum dolor sit</li>
  </ul>
  <div class="call">Call now</div>
</div>

<!-- About -->
<div class="eyebrow" style="left:84px;top:2902px;font-size:19px">About Us</div>
<h2 class="sec-title" style="left:84px;top:2932px;font-size:35px">About Marlow Care</h2>
<p class="about-body">At Marlow Health Collective, our mission is to provide compassionate and professional long-term healthcare services that empower individuals to maintain their highest level of independence, health, and well-being in the comfort of their own homes or ours, either through our licensed home healthcare agency - Marlow Homecare, or in our Adult Residential Care Home - Marlow Senior Living.</p>
<div class="btn-outline" style="left:83px;top:3197px;width:134px;height:41px;font-size:13.5px;gap:10px">Read more
  <svg width="11" height="11" viewBox="0 0 11 11"><path d="M1 10L10 1M4 1h6v6" fill="none" stroke="#f47f74" stroke-width="1.3"/></svg>
</div>
<div class="photo" role="img" aria-label="Photo of seniors doing crafts together in a bright living room" style="left:670px;top:2880px;width:447px;height:347px;background:linear-gradient(135deg,#6b4a2e,#c9bf6a 40%,#b5554a 65%,#d4c28c)"></div>

<!-- CTA -->
<section class="cta" role="img" aria-label="Photo of a smiling caregiver in a care home lounge">
  <div class="cta-inner">
    <h2>Schedule A Complimentary Care Consultation</h2>
    <p>If You're A DPhil Student Or Member Of Research Staff At The Northbridge Institute, You Can Join The Editorial Team! Please Contact Us To Find Out More.</p>
    <div class="btn-solid" style="left:450px;top:186px;width:220px;height:42px;font-size:13px">Contact Us</div>
  </div>
</section>

<!-- Footer -->
<footer>
  <div class="foot-brand" style="left:84px;color:var(--coral)"><span class="sq"></span>Marlow Homecare</div>
  <div class="foot-brand" style="left:316px;color:var(--ink)"><span class="sq"></span>Marlow Health Collective</div>
  <div class="foot-brand" style="left:620px;color:#4f9a94"><span class="sq"></span>Marlow Senior Living</div>

  <div class="abs" style="left:1016px;top:3633px;font-size:16px;font-weight:600;color:var(--coral)">Get In Touch</div>
  <div class="abs" style="left:1018px;top:3678px;display:flex;gap:10px">
    <span style="width:24px;height:24px;border-radius:50%;background:var(--coral);opacity:.85"></span>
    <span style="width:24px;height:24px;border-radius:50%;background:var(--coral);opacity:.85"></span>
    <span style="width:24px;height:24px;border-radius:4px;background:var(--coral);opacity:.85"></span>
  </div>

  <div class="foot-rule"></div>

  <div class="foot-head" style="left:84px">Pages</div>
  <div class="foot-col" style="left:84px">Home<br>About<br>Service<br>Blog</div>

  <div class="foot-head" style="left:164px">Services</div>
  <div class="foot-col" style="left:164px">Learn<br>Caregiver Jobs<br>Nurse Aide Care<br>24-Hour Home Care</div>
  <div class="foot-col" style="left:318px">Skilled Nursing<br>Lifestyle Aide<br>Hospice At Home<br>Bathing &amp; Meal Service</div>

  <div class="foot-head" style="left:480px">Contact Info</div>
  <div class="contact-row" style="top:3815px">
    <svg width="16" height="12" viewBox="0 0 16 12"><rect x=".5" y=".5" width="15" height="11" rx="1.5" fill="#f47f74"/><path d="M1 1.5l7 5 7-5" fill="none" stroke="#fff" stroke-width="1.2"/></svg>
    hello@marlowhealth-example.com</div>
  <div class="contact-row" style="top:3848px">
    <svg width="16" height="16" viewBox="0 0 16 16"><path d="M3 1.5l3 .5 1 3.5-2 1.3a9 9 0 004.2 4.2L10.5 9l3.5 1 .5 3-2 1.5C7 14 2 9 1.5 3.5z" fill="#f47f74"/></svg>
    808-555-0172</div>
  <div class="contact-row" style="top:3880px">
    <svg width="14" height="18" viewBox="0 0 14 18"><path d="M7 1a6 6 0 016 6c0 4.5-6 10-6 10S1 11.5 1 7a6 6 0 016-6z" fill="#f47f74"/><circle cx="7" cy="7" r="2.2" fill="#fff"/></svg>
    <span>248 Pueo Lane, Suite 310,<br>Honolulu, HI 96817</span></div>

  <div class="abs" style="left:746px;top:3773px;font-size:13px;font-weight:600;color:var(--coral)">Stay Connected</div>
  <div class="abs" style="left:746px;top:3802px;font-size:9px;color:var(--coral);opacity:.8">Get In Touch</div>
  <div class="abs" style="left:746px;top:3830px;width:251px;height:40px;border:1px solid var(--coral-soft);border-radius:6px;font-size:12.5px;color:#555;display:flex;align-items:center;padding-left:16px">Enter Your Email</div>
  <div class="abs" style="left:1002px;top:3830px;width:115px;height:40px;background:var(--coral);border-radius:6px;color:#fff;font-size:13px;font-weight:600;display:flex;align-items:center;justify-content:center">Subscribe</div>

  <div class="copyright">© 2024 Marlow Care All Rights Reserved.</div>
</footer>

</body>
</html>
```